Brightfield Homes needs a web design and brand identifier

Brightfield Homes is a pioneering approach by Victorian councils and four greenhouse alliances to support low income households to install solar systems with no upfront costs.

Brightfield Homes will commence in May 2017.

Brightfield Homes is looking for a designer to create a website banner incorporating a brand identifier for Brightfield Homes. The brand identifier will be used in Brightfield Homes promotional materials, such as flyers and mail outs.

The website banner and brand identifier should engender trust and confidence in the target group (retirees).

Reason: Hi, Thank you for your work so far. We've been given advice to get a separate logo designed (instead of trying to include this as part of the banner design). Sorry for not realising this until now - we're new to all this. So, I have a couple of preliminary logo designs that are being considered by our project control group. I will forward a copy of the logo once we have it. The project control group is looking for a web design that is unique to Brightfield Homes and a design that draws on the key elements of the program (i.e. it helps people save money and take control). The site should be friendly but not too informal as the target group is seniors. Here's a link to another community energy organisation: www.kindlewattnet.com.au/ Apologies again for the delays. Cheers, Doug

Target Market(s)

Home owning, low income, retirees

Industry/Entity Type

Non Profit

Number of Pages Required

1 page

Font styles to use
Sans Serif

Requirements
Must have
• Use of Brightfield Home name
• Must promote Brightfield Homes as safe, reliable and trustworthy
Nice to have
• Blue - to engender sense of safety and confidence (open to suggestions, though)
• Solar panels / the sun
Should not have
• Anything that is hard to read
• anything that promotes riskyness

```html
<!DOCTYPE html>
<html lang="en">
<head>
<meta charset="utf-8">
<title>Brightfield Home Supports Pensioners</title>
<link rel="stylesheet" href="https://fonts.googleapis.com/css2?family=Open+Sans:wght@300;400;600;700&family=Roboto+Condensed:wght@400&family=Raleway:wght@400&display=swap">
<style>
:root{
  --blue:#0a4c9c;
  --blue-bright:#1565c0;
  --navy:#0d2f6b;
  --ink:#1d1d1d;
  --text:#333;
  --grey-bg:#e9ecef;
  --dark:#1f2226;
  --footer:#25282c;
  --copy:#0a4fa6;
  --white:#fff;
}
*{box-sizing:border-box;margin:0;padding:0}
html,body{width:1200px;height:2961px;overflow:hidden}
body{font-family:"Open Sans",Arial,sans-serif;color:var(--text);background:var(--white);position:relative}
.abs{position:absolute}

/* header */
.site-header{position:absolute;left:0;top:0;width:1200px;height:112px;background:var(--white)}
.contact-pill{position:absolute;left:720px;top:0;width:405px;height:34px;background:var(--ink);border-radius:0 0 24px 24px;display:flex;align-items:center;justify-content:flex-start;gap:16px;color:#fff;font-size:14px;white-space:nowrap;overflow:hidden}
.contact-pill .mail{background:var(--blue);height:34px;display:flex;align-items:center;padding:0 16px 0 22px;border-radius:0 0 0 22px;gap:8px}
.contact-pill span{display:flex;align-items:center;gap:8px;white-space:nowrap}
.brand{position:absolute;left:80px;top:28px;display:flex;align-items:center;gap:12px;white-space:nowrap}
.brand-mark{width:60px;height:54px;background:var(--blue);border-radius:4px}
.brand-name{color:var(--ink);font-weight:700;font-size:26px;line-height:29px;letter-spacing:.4px}
.brand-name small{display:block;color:var(--blue);font-size:17px;line-height:21px;letter-spacing:.6px}
.main-nav{position:absolute;right:75px;top:64px;display:flex;gap:10px;font-size:13px;font-weight:600;color:var(--ink);white-space:nowrap}
.main-nav a{color:inherit;text-decoration:none;padding:4px 10px;border-radius:3px;white-space:nowrap}
.main-nav a.active{background:var(--blue);color:#fff}

/* hero */
.hero{position:absolute;left:0;top:112px;width:1200px;height:578px;background:linear-gradient(180deg,#7fb1e3 0%,#a9c9e6 30%,#5f7a4c 55%,#8a8f93 78%,#3b4652 100%)}
.hero-tag{position:absolute;left:89px;top:352px;width:262px;height:45px;background:var(--blue)}
.hero-caption{position:absolute;left:0;top:498px;width:1200px;height:80px;background:rgba(0,0,0,.35);color:#fff;font-family:"Roboto Condensed",Arial,sans-serif;font-size:21px;line-height:31px;text-align:center;padding-top:9px}

/* how it works */
.how{position:absolute;left:0;top:690px;width:1200px;height:490px;background:linear-gradient(180deg,#e4e6e9,#f4f5f7 40%,#dfe2e6)}
.section-title{position:absolute;left:0;width:1200px;text-align:center;font-family:"Raleway",Arial,sans-serif;font-size:36px;font-weight:400;color:var(--ink);letter-spacing:.5px}
.section-title b{font-weight:400;color:var(--blue)}
.title-rule{position:absolute;left:380px;width:440px;height:1px;background:#c9cdd2}
.title-rule::after{content:"";position:absolute;left:212px;top:-8px;width:16px;height:16px;background:#b8bcc2;border-radius:2px}
.how-lead{position:absolute;left:0;top:146px;width:1200px;text-align:center;font-size:16px;color:var(--ink)}
.how-lead b{color:var(--blue);font-weight:600}
.step{position:absolute;width:220px;text-align:center;font-size:13.5px;line-height:19px;color:var(--ink)}
.step-icon{position:absolute;width:122px;height:122px;border-radius:50%;background:#fff;box-shadow:0 4px 14px rgba(0,0,0,.18)}
.step-num{position:absolute;width:30px;height:30px;border-radius:50%;background:var(--blue);color:#fff;font-size:15px;font-weight:700;display:flex;align-items:center;justify-content:center}
.dash{position:absolute;top:272px;width:150px;height:20px}

/* blue band */
.expert-band{position:absolute;left:0;top:1180px;width:1200px;height:132px;background:linear-gradient(180deg,#1c6fc4,#0b4da0);color:#fff;text-align:center;font-size:22px;line-height:34px;padding-top:18px}
.cta{position:absolute;left:432px;top:1286px;width:336px;height:54px;border-radius:27px;background:var(--ink);border:3px solid #fff;color:#fff;font-weight:700;font-size:24px;letter-spacing:1px;display:flex;align-items:center;justify-content:center;white-space:nowrap}

/* services */
.services-lead{position:absolute;left:150px;top:1478px;width:900px;text-align:center;font-size:15px;line-height:25px;color:var(--ink)}
.service-img{position:absolute;top:1553px;height:192px;border-radius:8px;border:5px solid #f1f2f4;box-shadow:0 1px 5px rgba(0,0,0,.15)}
.service-name{position:absolute;top:1764px;width:340px;text-align:center;color:var(--blue);font-size:25px;letter-spacing:1px;white-space:nowrap}

/* eligible */
.eligible{position:absolute;left:0;top:1832px;width:1200px;height:281px;background:linear-gradient(100deg,#1f2a38 0%,#2c3a4c 55%,#55626f 80%,#3a4756 100%)}
.eligible h2{position:absolute;left:78px;top:48px;color:#fff;font-size:35px;font-weight:600}
.eligible .sub{position:absolute;left:82px;top:105px;color:#fff;font-size:17px}
.tick-item{position:absolute;color:#fff;font-size:15px;font-weight:600;display:flex;align-items:center;gap:14px;white-space:nowrap}

/* support */
.support-photo{position:absolute;left:70px;top:2125px;width:304px;height:452px;background:linear-gradient(180deg,#f3efec,#c7b3a4 35%,#2a2a2e 70%,#1b1b1e)}
.support h3{position:absolute;left:444px;top:2234px;font-size:25px;line-height:38px;color:var(--ink);font-weight:700;white-space:nowrap}
.support h3 span{color:var(--blue)}
.support-item{position:absolute;width:300px;font-size:15px;line-height:20px;color:var(--ink);padding-left:36px}
.support-item svg{position:absolute;left:0;top:0}

/* footer */
.site-footer{position:absolute;left:0;top:2577px;width:1200px;height:335px;background:linear-gradient(180deg,#1a1c1f,#2b2e33)}
.footer-col h4{position:absolute;top:56px;color:#fff;font-size:19px;font-weight:400}
.quick-links{position:absolute;left:86px;top:104px;list-style:none;font-size:13px;line-height:28.5px;color:#cfd3d8}
.quick-links li::before{content:"› ";color:#888}
.quick-links li.current{color:var(--blue-bright)}
.contact-line{position:absolute;left:306px;font-size:13px;line-height:17px;color:#d3d6da;padding-left:20px}
.contact-line svg{position:absolute;left:0;top:1px}
.field{position:absolute;border:1px solid #55595f;background:rgba(0,0,0,.2);color:#bbb;font-size:11px;padding:6px 8px}
.submit{position:absolute;left:586px;top:248px;width:82px;height:38px;background:var(--blue);color:#fff;font-size:13px;display:flex;align-items:center;justify-content:center}
.footer-brand{position:absolute;left:884px;top:96px;width:252px;text-align:center;color:#d8dbdf;font-size:17px;line-height:24px;font-weight:600}
.footer-brand .mark{width:56px;height:50px;margin:0 auto 16px;background:#d8dbdf;border-radius:4px}
.social{position:absolute;top:240px;width:38px;height:38px;border-radius:50%;background:var(--blue-bright);border:2px solid #fff}
.copyright{position:absolute;left:0;top:2912px;width:1200px;height:49px;background:var(--copy);color:#fff;font-size:14px;display:flex;align-items:center;justify-content:center}
</style>
</head>
<body>

<header class="site-header">
  <div class="contact-pill">
    <span class="mail"><svg width="16" height="12" viewBox="0 0 16 12"><rect x="0.5" y="0.5" width="15" height="11" fill="none" stroke="#fff"/><path d="M1 1l7 6 7-6" fill="none" stroke="#fff"/></svg>info@brightfieldhomes.org</span>
    <span><svg width="14" height="14" viewBox="0 0 14 14"><path d="M3 1l2 3-1.5 1.5a8 8 0 0 0 5 5L10 9l3 2-1.5 2.5C6 13 1 8 0.5 2.5z" fill="#fff"/></svg>123-555-0148</span>
  </div>
  <div class="brand">
    <div class="brand-mark"></div>
    <div class="brand-name">BRIGHTFIELD HOME<small>SUPPORTS PENSIONERS</small></div>
  </div>
  <nav class="main-nav">
    <a class="active">HOME</a><a>ABOUT US</a><a>CLIENTS</a><a>PROJECTS</a><a>TRAINING</a><a>CAREER</a><a>CONTACT US</a>
  </nav>
</header>

<section class="hero" role="img" aria-label="Photograph of an installer shaking hands with a retired couple beside rooftop solar panels, mountains behind">
  <div class="hero-tag"></div>
  <p class="hero-caption">Brightfield Homes Is A Pioneering Approach By Councils To Support Pensioner Households To  Save Money And Take Control<br>Of Their Energy Bills By Installing Affordable, Quality Solar Systems With No Upfront Costs.</p>
</section>

<section class="how">
  <h2 class="section-title" style="top:46px">HOW IT <b>WORKS</b></h2>
  <div class="title-rule" style="top:118px"></div>
  <p class="how-lead">We've done the hard work of finding a <b>safe</b>, <b>reliable</b> and <b>quality</b> installer so pensioners don't have to.</p>

  <div class="step-icon" style="left:113px;top:224px"></div>
  <div class="step-num" style="left:206px;top:222px">1</div>
  <svg class="abs" style="left:144px;top:255px" width="60" height="60" viewBox="0 0 60 60"><circle cx="30" cy="30" r="22" fill="none" stroke="#0a4c9c" stroke-width="5" stroke-dasharray="4 3"/><circle cx="30" cy="30" r="11" fill="none" stroke="#0a4c9c" stroke-width="4"/></svg>
  <div class="step-icon" style="left:391px;top:224px"></div>
  <div class="step-num" style="left:484px;top:222px">2</div>
  <svg class="abs" style="left:422px;top:255px" width="60" height="60" viewBox="0 0 60 60"><path d="M6 30L30 8l24 22" fill="none" stroke="#0a4c9c" stroke-width="5"/><path d="M14 26v26h32V26" fill="none" stroke="#0a4c9c" stroke-width="5"/><rect x="25" y="36" width="10" height="16" fill="#0a4c9c"/></svg>
  <div class="step-icon" style="left:677px;top:224px"></div>
  <div class="step-num" style="left:770px;top:222px">3</div>
  <svg class="abs" style="left:708px;top:255px" width="60" height="60" viewBox="0 0 60 60"><circle cx="30" cy="18" r="10" fill="none" stroke="#0a4c9c" stroke-width="5"/><path d="M6 38h14l10 6h18M6 50h40l10-10" fill="none" stroke="#0a4c9c" stroke-width="5"/></svg>
  <div class="step-icon" style="left:967px;top:224px"></div>
  <div class="step-num" style="left:1060px;top:222px">4</div>
  <svg class="abs" style="left:998px;top:255px" width="60" height="60" viewBox="0 0 60 60"><rect x="8" y="18" width="40" height="28" rx="3" fill="none" stroke="#0a4c9c" stroke-width="5" transform="rotate(-12 28 32)"/><rect x="14" y="24" width="40" height="28" rx="3" fill="#fff" stroke="#0a4c9c" stroke-width="5"/><path d="M14 32h40" stroke="#0a4c9c" stroke-width="5"/></svg>

  <svg class="dash" style="left:255px" viewBox="0 0 150 20"><path d="M2 14Q75 0 140 10" fill="none" stroke="#555" stroke-width="2" stroke-dasharray="4 4"/><path d="M136 5l8 6-9 3" fill="none" stroke="#555" stroke-width="2"/></svg>
  <svg class="dash" style="left:540px" viewBox="0 0 150 20"><path d="M2 14Q75 0 140 10" fill="none" stroke="#555" stroke-width="2" stroke-dasharray="4 4"/><path d="M136 5l8 6-9 3" fill="none" stroke="#555" stroke-width="2"/></svg>
  <svg class="dash" style="left:832px" viewBox="0 0 150 20"><path d="M2 14Q75 0 140 10" fill="none" stroke="#555" stroke-width="2" stroke-dasharray="4 4"/><path d="M136 5l8 6-9 3" fill="none" stroke="#555" stroke-width="2"/></svg>

  <p class="step" style="left:64px;top:362px">Brightfield Homes Checks That Every Person Gets A Solar System That Pays For Itself In Energy Savings From Day One</p>
  <p class="step" style="left:342px;top:362px">Brightfield Homes Organises For The Solar System To Be Installed</p>
  <p class="step" style="left:628px;top:362px">Brightfield Homes Supports Pensioners To Understand And Get The Most Out Of Solar</p>
  <p class="step" style="left:918px;top:362px">Pensioners Gradually Pay For Cost Through Their Usual Rates Payments At 0% Interest</p>
</section>

<section class="expert-band">
  We Are The Solar Experts In The Solar Kingdom. The Sunvale Region Solar Market Is<br>A Promising Market With Huge Potential
</section>
<div class="cta">GET IN TOUCH TODAY</div>

<section class="services">
  <h2 class="section-title" style="top:1374px">OUR <b>SERVICES</b></h2>
  <div class="title-rule" style="top:1446px"></div>
  <p class="services-lead">Over 20 Victorian councils have come together with support from the State Clean Power Futures Fund to run the Brightfield Home program.</p>
  <div class="service-img" style="left:72px;width:340px;background:linear-gradient(180deg,#5fb3ee,#bfe3f7 55%,#6aa646 80%,#d9a07a)" role="img" aria-label="Illustration of a hand holding a small green world with a solar panel and wind turbines under the sun"></div>
  <div class="service-img" style="left:428px;width:336px;background:linear-gradient(160deg,#7b6a4e,#2f5fb0 30%,#3a6cc2 70%,#1f3f7a)" role="img" aria-label="Photograph of workers installing rows of blue solar panels"></div>
  <div class="service-img" style="left:782px;width:338px;background:linear-gradient(120deg,#9aa3ac,#c8ced3 45%,#3b4654 70%,#e0b52c 85%,#7d8690)" role="img" aria-label="Photograph of an engineer in a hard hat and headphones working on machinery"></div>
  <p class="service-name" style="left:72px">RENEWABLE ENERGY</p>
  <p class="service-name" style="left:426px">PROCESS AUTOMATION</p>
  <p class="service-name" style="left:781px">GENERAL ENGINEERING</p>
</section>

<section class="eligible" role="img" aria-label="Background photograph of an installer fitting solar panels on a roof at dusk">
  <h2>Is My Client Eligible?</h2>
  <p class="sub">Refer clients who are:</p>
  <p class="tick-item" style="left:82px;top:150px"><svg width="22" height="18" viewBox="0 0 22 18"><path d="M2 9l6 6L20 2" fill="none" stroke="#fff" stroke-width="3"/></svg>Homeowners</p>
  <p class="tick-item" style="left:82px;top:192px"><svg width="22" height="18" viewBox="0 0 22 18"><path d="M2 9l6 6L20 2" fill="none" stroke="#fff" stroke-width="3"/></svg>Pension card holders</p>
  <p class="tick-item" style="left:308px;top:150px"><svg width="22" height="18" viewBox="0 0 22 18"><path d="M2 9l6 6L20 2" fill="none" stroke="#fff" stroke-width="3"/></svg>Usually at home from 9am to 5pm</p>
  <p class="tick-item" style="left:308px;top:192px"><svg width="22" height="18" viewBox="0 0 22 18"><path d="M2 9l6 6L20 2" fill="none" stroke="#fff" stroke-width="3"/></svg>Average to high electricity users (contact Brightfield Homes if unsure)</p>
</section>

<section class="support">
  <div class="support-photo" role="img" aria-label="Photograph of a smiling woman in a dark business jacket"></div>
  <h3>Brightfield Homes Will Support Councils To Install Solar<br><span>For Pension Card Households By:</span></h3>
  <p class="support-item" style="left:444px;top:2326px"><svg width="24" height="22" viewBox="0 0 24 22"><path d="M2 11l7 7L22 2" fill="none" stroke="#0a4c9c" stroke-width="3"/></svg>Coordinating Household Promotion &amp; Recruitment</p>
  <p class="support-item" style="left:444px;top:2394px"><svg width="24" height="22" viewBox="0 0 24 22"><path d="M2 11l7 7L22 2" fill="none" stroke="#0a4c9c" stroke-width="3"/></svg>Managing The Procurement Process To Contract A Solar Installer</p>
  <p class="support-item" style="left:444px;top:2458px"><svg width="24" height="22" viewBox="0 0 24 22"><path d="M2 11l7 7L22 2" fill="none" stroke="#0a4c9c" stroke-width="3"/></svg>Securing Lower Interest Finance Options For Households</p>
  <p class="support-item" style="left:832px;top:2326px;width:240px"><svg width="24" height="22" viewBox="0 0 24 22"><path d="M2 11l7 7L22 2" fill="none" stroke="#0a4c9c" stroke-width="3"/></svg>Responding To Householder Enquiries</p>
  <p class="support-item" style="left:832px;top:2394px;width:240px"><svg width="24" height="22" viewBox="0 0 24 22"><path d="M2 11l7 7L22 2" fill="none" stroke="#0a4c9c" stroke-width="3"/></svg>Administering The Installations</p>
  <p class="support-item" style="left:832px;top:2458px;width:240px"><svg width="24" height="22" viewBox="0 0 24 22"><path d="M2 11l7 7L22 2" fill="none" stroke="#0a4c9c" stroke-width="3"/></svg>Evaluating The Project</p>
</section>

<footer class="site-footer">
  <div class="footer-col"><h4 style="left:82px">Quick Links</h4></div>
  <ul class="quick-links">
    <li class="current">Home</li><li>About Us</li><li>Clients</li><li>Projects</li><li>Training</li><li>Career</li><li>Contact</li>
  </ul>
  <div class="footer-col"><h4 style="left:303px">Contact Details</h4></div>
  <p class="contact-line" style="top:104px"><svg width="12" height="16" viewBox="0 0 12 16"><path d="M6 0a6 6 0 0 1 6 6c0 4-6 10-6 10S0 10 0 6a6 6 0 0 1 6-6z" fill="#1565c0"/><circle cx="6" cy="6" r="2" fill="#fff"/></svg>Brightfield Home Supports Pensioners<br><span style="color:#9a9ea4">Harbour Road Eastern District 31000<br>Sunvale Region</span></p>
  <p class="contact-line" style="top:186px"><svg width="14" height="14" viewBox="0 0 14 14"><path d="M3 1l2 3-1.5 1.5a8 8 0 0 0 5 5L10 9l3 2-1.5 2.5C6 13 1 8 0.5 2.5z" fill="#1565c0"/></svg>555130084120</p>
  <p class="contact-line" style="top:260px"><svg width="14" height="11" viewBox="0 0 14 11"><rect width="14" height="11" fill="#1565c0"/><path d="M1 1l6 5 6-5" fill="none" stroke="#fff"/></svg>hello@brightfieldhomes.org</p>
  <div class="footer-col"><h4 style="left:586px">Quick Inquiry</h4></div>
  <div class="field" style="left:586px;top:108px;width:138px;height:36px">Name</div>
  <div class="field" style="left:730px;top:108px;width:134px;height:36px">Phone</div>
  <div class="field" style="left:586px;top:152px;width:278px;height:84px">Message</div>
  <div class="submit">SUBMIT</div>
  <div class="footer-brand"><div class="mark"></div>BRIGHTFIELD HOME<br>SUPPORTS PENSIONERS</div>
  <div class="social" style="left:928px" role="img" aria-label="Social link"></div>
  <div class="social" style="left:970px" role="img" aria-label="Social link"></div>
  <div class="social" style="left:1012px" role="img" aria-label="Social link"></div>
  <div class="social" style="left:1054px" role="img" aria-label="Social link"></div>
</footer>
<div class="copyright">Copyright © 2016 BRIGHTFIELD HOME SUPPORTS PENSIONERS. All Rights Reserved.</div>

</body>
</html>
```